Business Card Design Project

This is the first time we use our new logo. We need a business card that we can use both on our institutional corporate relationships and also that works for our staff that deals with consumers directly.

VELUNDA is a new company dedicated to empower consumers and to provide them with the best choices for specialized health care using the latest telemedicine technology (medicine at a distance via videoconference).

We want to print this cards in high quality materials and process. We will like designs that allow us to use UV spot varnish and other techniques that will differentiate us.

We are including Two different versions of Color logos. In addition we are including white over black background logos. Those can be used replacing the black for a color.

Please note this is the first time we will be creating any corporate materials with our new logo and colors.

Target Market(s)

34+ consumers of medium high and high socioeconomic levels.

Industry/Entity Type

Health

Requirements
Must have
• Our logo on its original colors
Should not have
• Any other graphical element or design that is not our logo

```html
<!DOCTYPE html>
<html lang="en">
<head>
<meta charset="utf-8">
<title>VELUNDA business cards</title>
<link rel="stylesheet" href="https://fonts.googleapis.com/css2?family=Jost:ital,wght@0,400;0,500;0,600;1,600&display=swap">
<style>
  :root {
    --backdrop: #e9e6e1;
    --brand-blue: #1d5a84;
    --brand-sky: #5ab4e0;
    --ink: #1a1a1a;
    --ink-soft: #3a3a3a;
    --white: #ffffff;
    --silver-1: #c9c9c9;
    --silver-2: #e6e6e6;
    --silver-3: #b8b8b8;
    --steel-dark: #2b2b2b;
    --steel-mid: #8a8a8a;
    --steel-light: #dcdcdc;
  }
  * { margin: 0; padding: 0; box-sizing: border-box; }
  html, body { width: 788px; height: 1200px; overflow: hidden; }
  body {
    position: relative;
    background: var(--backdrop);
    font-family: "Jost", "Futura", sans-serif;
  }
  .card {
    position: absolute;
    width: 300px;
    height: 525px;
    border-radius: 18px;
    overflow: hidden;
    text-align: center;
  }
  .card--silver-front {
    left: 69px; top: 45px;
    background:
      repeating-linear-gradient(90deg, rgba(255,255,255,0.18) 0 1px, transparent 1px 3px),
      linear-gradient(120deg, var(--silver-1), var(--silver-2) 45%, var(--silver-3));
  }
  .card--white {
    left: 432px; top: 45px;
    background: var(--white);
    box-shadow: 0 0 0 1px #dcdcdc;
  }
  .card--steel {
    left: 69px; top: 628px;
    background:
      repeating-linear-gradient(0deg, rgba(255,255,255,0.07) 0 1px, transparent 1px 3px),
      linear-gradient(100deg, var(--steel-dark), var(--steel-mid) 45%, var(--steel-light));
  }
  .card--blue {
    left: 430px; top: 632px;
    background: var(--brand-blue);
  }
  .holder-name {
    position: absolute; top: 26px; left: 0; right: 0;
    font-size: 17px; font-weight: 600; color: var(--ink);
  }
  .holder-role {
    position: absolute; top: 48px; left: 0; right: 0;
    font-size: 13px; color: var(--ink);
  }
  .brand-dot {
    position: absolute; left: 50%;
    width: 26px; height: 26px; margin-left: -13px;
    border-radius: 50%;
    background: var(--brand-sky);
  }
  .brand-name {
    position: absolute; left: 0; right: 0;
    font-weight: 600; letter-spacing: 2px; line-height: 1;
    color: var(--brand-blue);
  }
  .card--silver-front .brand-dot { top: 190px; }
  .card--silver-front .brand-name { top: 252px; font-size: 42px; }
  .card--white .brand-dot { top: 190px; }
  .card--white .brand-name { top: 280px; font-size: 46px; }
  .card--steel .brand-dot { top: 200px; width: 34px; height: 34px; margin-left: -17px; background: var(--white); }
  .card--steel .brand-name { top: 258px; font-size: 46px; color: var(--white); }
  .card--blue .brand-dot { top: 210px; }
  .card--blue .brand-name { top: 293px; font-size: 42px; color: var(--white); }
  .contact {
    position: absolute; top: 352px; left: 0; right: 0;
    list-style: none; font-size: 14px; color: var(--ink); line-height: 26px;
  }
  .contact b { font-weight: 600; font-style: italic; }
  .contact .address { line-height: 17px; margin-top: 4px; }
  .web {
    position: absolute; bottom: 28px; left: 0; right: 0;
    font-size: 16px; letter-spacing: 0.3px;
  }
  .card--white .web { color: var(--ink-soft); }
  .card--steel .web, .card--blue .web { color: var(--white); }
</style>
</head>
<body>
  <section class="card card--silver-front">
    <p class="holder-name">Your Name</p>
    <p class="holder-role">Designation</p>
    <span class="brand-dot"></span>
    <p class="brand-name">VELUNDA</p>
    <ul class="contact">
      <li><b>phone</b> : +12 345 67890</li>
      <li><b>fax</b> : +12 345 67890</li>
      <li><b>email</b> : info@velundahealth.com</li>
      <li><b>web</b> : www.velundahealth.com</li>
      <li class="address">#0000, Street Name<br>Area Name, Country Code</li>
    </ul>
  </section>

  <section class="card card--white">
    <span class="brand-dot"></span>
    <p class="brand-name">VELUNDA</p>
    <p class="web">www.velundahealth.com</p>
  </section>

  <section class="card card--steel">
    <span class="brand-dot"></span>
    <p class="brand-name">VELUNDA</p>
    <p class="web">www.velundahealth.com</p>
  </section>

  <section class="card card--blue">
    <span class="brand-dot"></span>
    <p class="brand-name">VELUNDA</p>
    <p class="web">www.velundahealth.com</p>
  </section>
</body>
</html>
```